Business Card Design for sports performance / psychology company

You can see my website that this is based upon here:
http://www.trelvanedge.co.uk

More than happy to answer any additional questions that you might have

** Happy for any images from Pixelvault to be used. If I go with your design I will purchase the image for you to use

Target Market(s)

Football players

Industry/Entity Type

Business

Contact Information for Business Card

Name: Clive Arnott
Title: Clinical Hypnotherapist & Strategist
Email address: clive@trelvanedge.co.uk
Tel: 07912486015

Font styles to use
Other font styles liked:
• Same font as on website. I'm not actually sure what it is

Requirements
Must have
• Tagline:
• Talent x Focus = Results
• Don't put form down to chance
Nice to have
• Happy for designers to be creative
Should not have

```html
<!DOCTYPE html>
<html lang="en">
<head>
<meta charset="utf-8">
<title>Trelvan Edge – Business Card</title>
<link rel="stylesheet" href="https://fonts.googleapis.com/css2?family=Jost:wght@400&family=Lato:wght@400;700&display=swap">
<style>
  :root {
    --bg: #222222;
    --navy: #221c4a;
    --navy-ink: #1f1a45;
    --white: #ffffff;
    --grey-text: #3a3a42;
    --panel: #f2f2f6;
    --photo-a: #f4f4f5;
    --photo-b: #3e4048;
  }
  * { box-sizing: border-box; margin: 0; padding: 0; }
  html, body { width: 1189px; height: 1200px; overflow: hidden; background: var(--bg); }
  .canvas { position: relative; width: 1189px; height: 1200px; }

  .card { position: absolute; left: 171px; width: 856px; height: 488px; box-shadow: 0 6px 14px rgba(0,0,0,.55); }
  .card--front { top: 68px; background: var(--navy); color: var(--white); }
  .card--back { top: 626px; background: var(--white); overflow: hidden; }

  .front__mark { position: absolute; left: 390px; top: 168px; width: 76px; height: 76px; border: 3px solid var(--white); border-radius: 4px; }
  .front__wordmark { position: absolute; left: 0; right: 0; top: 256px; text-align: center; font: 400 66px/1 "Jost", sans-serif; letter-spacing: 2px; }
  .front__social { position: absolute; top: 382px; left: 0; right: 0; display: flex; justify-content: center; gap: 20px; }
  .front__social span { width: 34px; height: 34px; background: var(--white); border-radius: 2px; }

  .back__panel { position: absolute; left: 345px; top: 0; right: 0; bottom: 0; background: linear-gradient(90deg, var(--white) 0%, var(--panel) 100%); }
  .back__photo { position: absolute; left: 0; top: 0; width: 345px; height: 488px; background: linear-gradient(180deg, var(--photo-a) 0%, var(--photo-a) 20%, #cdb8a8 50%, #8a8f9c 75%, var(--photo-b) 100%); }
  .back__info { position: absolute; left: 394px; top: 70px; color: var(--grey-text); font-family: "Lato", sans-serif; }
  .back__wordmark { font: 400 42px/1 "Jost", sans-serif; color: var(--navy-ink); letter-spacing: 1px; }
  .back__tagline { font-size: 23px; line-height: 1.2; margin-top: 4px; }
  .back__name { font: 400 36px/1 "Lato", sans-serif; color: var(--navy-ink); margin-top: 70px; }
  .back__name strong { font-weight: 700; }
  .back__role { font-size: 22px; line-height: 1.2; margin-top: 2px; }
  .back__address { font-size: 22px; line-height: 28px; margin-top: 28px; }
  .back__contacts { list-style: none; margin-top: 14px; font-size: 22px; line-height: 28px; }
  .back__contacts li { display: flex; align-items: center; gap: 11px; }
  .contact__icon { width: 24px; height: 22px; background: var(--navy-ink); display: flex; align-items: center; justify-content: center; }
  .contact__icon svg { width: 16px; height: 14px; }
  .web__domain { color: var(--navy-ink); font-weight: 700; }
</style>
</head>
<body>
<main class="canvas">
  <section class="card card--front">
    <div class="front__mark"></div>
    <h1 class="front__wordmark">TRELVAN EDGE</h1>
    <div class="front__social"><span></span><span></span><span></span></div>
  </section>

  <section class="card card--back">
    <div class="back__panel"></div>
    <div class="back__photo" role="img" aria-label="Portrait photograph of Clive Arnott in a dark check jacket and light blue shirt"></div>
    <div class="back__info">
      <h2 class="back__wordmark">TRELVAN EDGE</h2>
      <p class="back__tagline">Talent x Focus = Results</p>
      <p class="back__name"><strong>Clive</strong> Arnott</p>
      <p class="back__role">Clinical Hypnotherapist &amp; Strategist</p>
      <p class="back__address">Tamar Innovation Park<br>Tavistock &amp; Wimpole Row, Bristol</p>
      <ul class="back__contacts">
        <li><span class="contact__icon"><svg viewBox="0 0 16 14"><path d="M2 5c0-2 3-3 6-3s6 1 6 3v1h-3V5H5v1H2z M4 7h8l1 5H3z" fill="#fff"/></svg></span>07912486015</li>
        <li><span class="contact__icon"><svg viewBox="0 0 16 14"><rect x="1.5" y="2.5" width="13" height="9" fill="none" stroke="#fff"/><path d="M1.5 2.5l6.5 5 6.5-5M1.5 11.5l5-4.5M14.5 11.5l-5-4.5" fill="none" stroke="#fff"/></svg></span>clive@trelvanedge.co.uk</li>
        <li><span class="contact__icon"><svg viewBox="0 0 16 14"><circle cx="8" cy="7" r="5.5" fill="none" stroke="#fff"/><ellipse cx="8" cy="7" rx="2.5" ry="5.5" fill="none" stroke="#fff"/><path d="M2.5 7h11M3.5 4h9M3.5 10h9" stroke="#fff"/></svg></span><span>www.<span class="web__domain">trelvanedge</span>.co.uk</span></li>
      </ul>
    </div>
  </section>
</main>
</body>
</html>
```